Brimsett Gardening Fresh New Website

We are looking to create a simple fresh website for our landscaping business. The website should appeal to a 'high end' audience. We deal with a lot of Embassies and affluent clients who have extremely large gardens that are meticulously maintained. The site is about communicating our excellent landscaping and customer service skills and encouraging new clients to reach out and engage us to take care of their gardens.

The website is basically going to be our business card, it will have almost no functionality other than two 'contact us' forms, one for smaller clients and one for more detailed projects.

The website will not have a lot of written content and will have to show photos of beautifully landscaped gardens.

The main logo in black will influence the site, however, we are open to all suggestions.

We are expecting to have the following pages:
Home Page
Services
About Us
Contact Us
Showcase (photo gallery of our work)

We need someone who can code it to wordpress and be available for minor changes over a number of days. They will be simple tweaks.

```html
<!DOCTYPE html>
<html lang="en">
<head>
<meta charset="utf-8">
<title>Brimsett Gardening</title>
<link href="https://fonts.googleapis.com/css2?family=Cinzel:wght@400;500&family=Poppins:wght@400;500;600&display=swap" rel="stylesheet">
<style>
:root{
  --black:#050505;
  --ink:#0b0b0b;
  --gold:#e8b923;
  --gold-deep:#b8860b;
  --white:#ffffff;
  --muted:#c9c9c9;
  --brown:#241b04;
  --field-line:#e0b321;
  --book-top:#8f6d0a;
  --book-bottom:#d6aa1a;
}
*{box-sizing:border-box;margin:0;padding:0}
html,body{width:1200px;height:3898px;overflow:hidden;background:var(--black)}
body{position:relative;font-family:'Poppins',sans-serif;color:var(--white)}
.abs{position:absolute}
.heading{font-family:'Cinzel',serif;font-weight:400;text-align:center;letter-spacing:1px;color:var(--white)}
.heading .accent{color:var(--gold)}
.rule{position:absolute;height:3px;width:54px;background:var(--gold);left:50%;margin-left:-27px}
.btn{position:absolute;display:flex;align-items:center;justify-content:center;border:2px solid var(--gold);border-radius:26px;color:var(--gold);font-size:15px;font-weight:500;text-transform:uppercase}

/* header */
.brand{position:absolute;display:flex;align-items:center;gap:14px}
.brand-dot{width:40px;height:40px;border-radius:50%;border:2px solid var(--gold)}
.brand-name{font-family:'Cinzel',serif;font-weight:500;color:var(--gold);letter-spacing:8px;line-height:1.25}
.brand-name .top{font-size:24px;display:block}
.brand-name .sub{font-size:13px;display:block;letter-spacing:9px}
.nav{position:absolute;left:0;width:1200px;height:20px;font-size:14px}
.nav a{position:absolute;transform:translateX(-50%);color:var(--white);text-decoration:none;white-space:nowrap}
.nav a.active{color:var(--gold)}
.nav a.active::after{content:"";position:absolute;left:0;right:0;bottom:-10px;height:2px;background:var(--white)}

/* hero */
.hero-photo{left:0;top:0;width:1200px;height:730px;background:linear-gradient(180deg,#1d2a12 0%,#3f6a22 30%,#5d8f2e 55%,#7eae3a 80%,#9cc44b 100%)}
.hero-title{top:182px;left:0;width:1200px}
.hero-title .l1{font-size:46px;display:block;line-height:1.2}
.hero-title .l2{font-size:58px;display:block;color:var(--gold);line-height:1.1}

/* about */
.about-photo{left:126px;top:812px;width:454px;height:400px;border-radius:40px 0 40px 0;background:linear-gradient(160deg,#5b8f2a,#7fb23f 50%,#4c7b22)}
.about-frame{left:113px;top:825px;width:454px;height:400px;border-left:9px solid var(--gold-deep);border-bottom:9px solid var(--gold-deep);border-radius:0 0 0 40px}
.about-title{left:635px;top:846px;font-size:44px;text-align:left}
.about-text{left:639px;top:934px;width:450px;font-size:15.5px;line-height:22px;color:var(--muted)}
.about-text p+p{margin-top:22px}

/* services */
.svc{position:absolute;width:310px;height:310px;border-radius:50%;overflow:hidden}
.svc .img{position:absolute;inset:0}
.svc .ring{position:absolute;inset:14px;border:1.5px solid var(--gold);border-radius:50%}
.svc .label{position:absolute;left:0;right:0;top:232px;text-align:center;font-weight:600;font-size:18px;text-shadow:0 1px 3px rgba(0,0,0,.6)}

/* forms */
.field{position:absolute;border:1.5px solid var(--field-line);display:flex;align-items:center;padding-left:30px;font-size:13.5px;color:var(--white)}
.field.sm{font-size:12.5px;padding-left:20px}
.field .icon{position:absolute;right:18px;top:50%;transform:translateY(-50%)}
.gallery-img{position:absolute;height:247px}

/* footer */
.footer-rule{left:119px;top:3799px;width:950px;height:1px;background:#3a3a3a}
.copyright{left:135px;top:3829px;font-size:11.5px;color:var(--white)}
.social{position:absolute;top:3824px;width:30px;height:30px;border-radius:50%;border:1.5px solid var(--white)}
</style>
</head>
<body>

<!-- HERO -->
<div class="abs hero-photo" role="img" aria-label="Photo of a terraced garden with curved stone retaining walls, flower beds and lawn"></div>
<div class="abs" style="left:0;top:0;width:1200px;height:130px;background:linear-gradient(180deg,rgba(5,5,5,.85),rgba(5,5,5,0))"></div>
<svg class="abs" style="left:0;top:600px" width="1200" height="150" viewBox="0 0 1200 150">
  <path d="M0 100 C 250 150, 450 120, 650 70 C 850 20, 1050 20, 1200 120 L1200 150 L0 150 Z" fill="var(--gold)"/>
  <path d="M0 110 C 250 162, 450 130, 650 82 C 850 34, 1050 36, 1200 135 L1200 150 L0 150 Z" fill="var(--black)"/>
</svg>

<div class="brand" style="left:106px;top:22px">
  <span class="brand-dot"></span>
  <span class="brand-name"><span class="top">BRIMSETT</span><span class="sub">GARDENING</span></span>
</div>
<nav class="nav" style="top:48px">
  <a class="active" style="left:446px">HOME</a>
  <a style="left:557px">SERVICES</a>
  <a style="left:700px">ABOUT US</a>
  <a style="left:856px">CONTACT US</a>
  <a style="left:1020px">SHOWCASE</a>
</nav>

<h1 class="abs heading hero-title"><span class="l1">WELCOME TO</span><span class="l2">BRIMSETT GARDENING</span></h1>
<div class="btn" style="left:499px;top:315px;width:184px;height:50px">Contact Us</div>

<!-- ABOUT -->
<div class="abs about-frame"></div>
<div class="abs about-photo" role="img" aria-label="Aerial photo of a lawn with a winding stepping-stone path being mowed"></div>
<h2 class="abs heading about-title">BRIMSETT <span class="accent">GARDENING</span></h2>
<div class="abs" style="left:639px;top:908px;width:54px;height:3px;background:var(--gold)"></div>
<div class="abs about-text">
  <p>Lorem ipsum dolor sit amet, consectetur adipiscing elit, sed do eiusmod tempor incididunt ut labore et dolore magna aliqua. Quis ipsum suspendisse ultrices gravida. Risus commodo viverra maecenas accumsan lacus vel facilisis.</p>
  <p>gravida. Risus commodo viverra maecenas accumsan lacus vel facilisis. Lorem ipsum dolor sit amet, consectetur adipiscing elit, sed do eiusmod tempor incididun</p>
</div>
<div class="btn" style="left:641px;top:1136px;width:187px;height:52px">Learn More</div>

<!-- SERVICES -->
<h2 class="abs heading" style="left:0;top:1330px;width:1200px;font-size:44px">OUR <span class="accent">SERVICES</span></h2>
<div class="rule" style="top:1390px"></div>

<div class="svc" style="left:107px;top:1429px">
  <div class="img" role="img" aria-label="Photo of a curved stone block flower bed on a lawn" style="background:linear-gradient(150deg,#4f7d2a,#b69a6a 55%,#6a9a32)"></div>
  <div class="ring"></div><div class="label">LANDSCAPING</div>
</div>
<div class="svc" style="left:444px;top:1429px">
  <div class="img" role="img" aria-label="Photo of a roll of turf being laid on soil" style="background:linear-gradient(150deg,#6e9a3c,#8a7350 50%,#4a3a25)"></div>
  <div class="ring"></div><div class="label">SERVICE TITLE</div>
</div>
<div class="svc" style="left:782px;top:1429px">
  <div class="img" role="img" aria-label="Photo of a paved garden path curving through a lawn" style="background:linear-gradient(150deg,#6aa43a,#8f9290 55%,#5c8d2c)"></div>
  <div class="ring"></div><div class="label">SERVICE TITLE</div>
</div>

<!-- CONTACT -->
<div class="abs" style="left:0;top:1804px;width:1200px;height:420px;background:var(--brown)"></div>
<svg class="abs" style="left:0;top:2150px" width="1200" height="110" viewBox="0 0 1200 110">
  <path d="M0 40 C 300 -10, 500 0, 800 10 C 1000 16, 1120 20, 1200 40 L1200 110 L0 110 Z" fill="var(--ink)"/>
</svg>
<div class="abs" style="left:0;top:2200px;width:1200px;height:785px;background:var(--ink)"></div>

<h2 class="abs heading" style="left:0;top:1860px;width:1200px;font-size:36px">CONTACT US</h2>
<div class="rule" style="top:1911px"></div>
<div class="field" style="left:251px;top:1955px;width:341px;height:53px">First Name</div>
<div class="field" style="left:610px;top:1955px;width:341px;height:53px">Last Name</div>
<div class="field" style="left:251px;top:2020px;width:341px;height:53px">Type of Service</div>
<div class="field" style="left:610px;top:2020px;width:341px;height:53px">Address</div>
<div class="btn" style="left:516px;top:2096px;width:186px;height:50px">Send Mesage</div>

<!-- GALLERY -->
<h2 class="abs heading" style="left:0;top:2262px;width:1200px;font-size:44px">OUR <span class="accent">GALLERY</span></h2>
<div class="rule" style="top:2320px"></div>
<div class="gallery-img" style="left:79px;top:2366px;width:331px;background:linear-gradient(160deg,#7ba43a,#8f6f7c 40%,#c08850)" role="img" aria-label="Photo of a planted garden bed beside a herringbone brick path"></div>
<div class="gallery-img" style="left:431px;top:2366px;width:332px;background:linear-gradient(160deg,#9aa0a0,#6f9a3a 55%,#b13a2a 70%,#4f8a2a)" role="img" aria-label="Photo of a wheelbarrow and spade on a lawn in front of a house"></div>
<div class="gallery-img" style="left:781px;top:2366px;width:331px;background:linear-gradient(160deg,#6d9a48,#b9b3a8 45%,#6b3e22)" role="img" aria-label="Photo of gloved hands planting a shrub in mulch"></div>
<div class="gallery-img" style="left:83px;top:2634px;width:333px;background:linear-gradient(160deg,#5c8a2c,#a8a8a4 50%,#6d4a2c)" role="img" aria-label="Photo of timber garden steps with gravel and rocks"></div>
<div class="gallery-img" style="left:436px;top:2634px;width:333px;background:linear-gradient(160deg,#8a8f8a,#3f7a2a 40%,#c24a5a 60%,#6fa83a)" role="img" aria-label="Photo of a stone-edged flower bed in front of a house"></div>
<div class="gallery-img" style="left:785px;top:2634px;width:333px;background:linear-gradient(160deg,#8a8a80,#4c7f2c 40%,#8fc043 80%)" role="img" aria-label="Photo of a front lawn with colourful planted borders"></div>

<!-- BOOK -->
<div class="abs" style="left:0;top:2985px;width:1200px;height:700px;background:linear-gradient(180deg,var(--book-top),var(--book-bottom))"></div>
<h2 class="abs heading" style="left:0;top:3045px;width:1200px;font-size:38px">BOOK A PROJECT WITH US</h2>
<div class="rule" style="top:3095px"></div>
<div class="field sm" style="left:194px;top:3129px;width:396px;height:56px">First Name</div>
<div class="field sm" style="left:601px;top:3129px;width:398px;height:56px">Last Name</div>
<div class="field sm" style="left:194px;top:3198px;width:396px;height:56px">Email address</div>
<div class="field sm" style="left:601px;top:3198px;width:398px;height:56px">Phone</div>
<div class="field sm" style="left:194px;top:3267px;width:396px;height:57px">List of Services</div>
<div class="field sm" style="left:601px;top:3267px;width:199px;height:57px">Select Date
  <svg class="icon" width="16" height="16" viewBox="0 0 16 16"><rect x="1.5" y="3" width="13" height="11.5" fill="none" stroke="#fff" stroke-width="1.4"/><line x1="1.5" y1="6.5" x2="14.5" y2="6.5" stroke="#fff" stroke-width="1.4"/><line x1="5" y1="1" x2="5" y2="4" stroke="#fff" stroke-width="1.4"/><line x1="11" y1="1" x2="11" y2="4" stroke="#fff" stroke-width="1.4"/></svg>
</div>
<div class="field sm" style="left:798px;top:3267px;width:201px;height:57px">Select Time
  <svg class="icon" width="16" height="16" viewBox="0 0 16 16"><circle cx="8" cy="8" r="6.5" fill="none" stroke="#fff" stroke-width="1.4"/><path d="M8 4.5 V8 H11" fill="none" stroke="#fff" stroke-width="1.4"/></svg>
</div>
<div class="field sm" style="left:194px;top:3330px;width:805px;height:56px">Address</div>
<div class="field sm" style="left:194px;top:3395px;width:805px;height:82px;align-items:flex-start;padding-top:14px">Message</div>
<div class="abs" style="left:505px;top:3492px;width:191px;height:51px;border-radius:26px;background:var(--black);color:var(--gold);display:flex;align-items:center;justify-content:center;font-size:15px;font-weight:500">SEND MESAGE</div>

<!-- FOOTER -->
<svg class="abs" style="left:0;top:3590px" width="1200" height="110" viewBox="0 0 1200 110">
  <path d="M0 50 C 250 10, 500 20, 750 50 C 950 72, 1100 60, 1200 40 L1200 110 L0 110 Z" fill="var(--black)"/>
</svg>
<div class="abs" style="left:0;top:3680px;width:1200px;height:218px;background:var(--black)"></div>

<div class="brand" style="left:119px;top:3705px">
  <span class="brand-dot"></span>
  <span class="brand-name"><span class="top">BRIMSETT</span><span class="sub">GARDENING</span></span>
</div>
<nav class="nav" style="top:3723px">
  <a style="left:446px">HOME</a>
  <a style="left:557px">SERVICES</a>
  <a style="left:700px">ABOUT US</a>
  <a style="left:856px">CONTACT US</a>
  <a style="left:1020px">SHOWCASE</a>
</nav>
<div class="abs footer-rule"></div>
<div class="abs copyright">© 2024 Company Name | All Rights Reserved</div>
<span class="social" style="left:958px"></span>
<span class="social" style="left:994px"></span>
<span class="social" style="left:1031px"></span>

</body>
</html>
```